Kestrel Home Business Card Design

We need a business card for a Building company based in Queensland, Australia. Our colours are orange black and we do base all our homes design names and other aspect of our business on astrology. We want the consumer to perceive the company as professional and to attract investors to our company.We have over 20 years in the building industry.We pride ourselves on our innovation of designs and making the building process for anyone from families to investor a smooth and simple experience.
Business
Amelia Prichard0411752116PO Box 454, Mudgeerbaameliaprichard@zodiachomes.com

```html
<!DOCTYPE html>
<html lang="en">
<head>
<meta charset="utf-8">
<title>Kestrel Homes Business Card</title>
<link rel="stylesheet" href="https://fonts.googleapis.com/css2?family=Source+Sans+3:wght@400;600;700&display=swap">
<style>
  :root {
    --backdrop: #3b3431;
    --card-front: #141414;
    --card-back: #3d3d3d;
    --orange: #f7941d;
    --white: #ffffff;
    --soft-white: #e9e9e9;
    --divider: #4a4a4a;
  }
  * { margin: 0; padding: 0; box-sizing: border-box; }
  html, body {
    width: 1200px; height: 844px; overflow: hidden;
    background: var(--backdrop);
    font-family: "Source Sans 3", "Myriad Pro", Arial, sans-serif;
  }
  .stage {
    position: relative; width: 1200px; height: 844px;
    display: flex; justify-content: center; align-items: center; gap: 50px;
  }
  .card {
    position: relative; width: 525px; height: 300px;
    box-shadow: 0 14px 30px rgba(0,0,0,0.45);
  }
  .card--front { background: var(--card-front); color: var(--white); }
  .card--back {
    background: var(--card-back);
    display: flex; flex-direction: column; align-items: center; justify-content: center; gap: 18px;
  }
  .brand-mark {
    position: absolute; left: 50%; top: 30px; transform: translateX(-50%);
    width: 58px; height: 58px; border-radius: 50%;
    background: var(--orange); border: 3px solid var(--white);
  }
  .brand-name {
    position: absolute; left: 0; right: 0; top: 98px;
    text-align: center; font-weight: 700; font-size: 36px; letter-spacing: 0.5px;
  }
  .details {
    position: absolute; left: 0; right: 0; top: 160px;
    display: flex; justify-content: center;
  }
  .person {
    width: 220px; text-align: right; padding-right: 16px;
    border-right: 1px solid var(--divider);
  }
  .person__name { font-weight: 700; font-size: 22px; line-height: 1.1; }
  .person__role { color: var(--orange); font-size: 15px; margin-bottom: 8px; }
  .person__address { font-size: 15px; line-height: 1.2; color: var(--soft-white); }
  .contacts { list-style: none; padding-left: 16px; width: 220px; }
  .contacts li {
    display: flex; align-items: center; gap: 9px;
    font-size: 14.5px; line-height: 1; height: 22px; color: var(--soft-white);
  }
  .contacts svg { width: 15px; height: 15px; flex: none; }
  .back-mark {
    width: 150px; height: 150px; border-radius: 50%;
    background: var(--orange); border: 5px solid var(--white);
  }
  .back-name { color: var(--white); font-weight: 700; font-size: 30px; }
</style>
</head>
<body>
<main class="stage">
  <section class="card card--front" aria-label="Business card front">
    <div class="brand-mark"></div>
    <h1 class="brand-name">Kestrel Homes</h1>
    <div class="details">
      <div class="person">
        <p class="person__name">Harriet Colvane</p>
        <p class="person__role">Managing Director</p>
        <p class="person__address">12345, Address Goes Here<br>Country Name, 123456</p>
      </div>
      <ul class="contacts">
        <li>
          <svg viewBox="0 0 16 16"><rect width="16" height="16" rx="2" fill="#f7941d"/><path d="M4 6c0-1 1-2 4-2s4 1 4 2v1h-2V6H6v1H4z M5 8h6l1 4H4z" fill="#141414"/></svg>
          (044)-456-7890
        </li>
        <li>
          <svg viewBox="0 0 16 16"><rect width="16" height="16" rx="2" fill="#f7941d"/><rect x="5" y="3" width="6" height="10" rx="1" fill="#141414"/><rect x="6" y="4.5" width="4" height="6" fill="#f7941d"/></svg>
          123-456-7890
        </li>
        <li>
          <svg viewBox="0 0 16 16"><rect width="16" height="16" rx="2" fill="#f7941d"/><rect x="3" y="5" width="10" height="7" fill="#141414"/><path d="M3 5l5 4 5-4" stroke="#f7941d" stroke-width="1" fill="none"/></svg>
          info@youremail.example
        </li>
        <li>
          <svg viewBox="0 0 16 16"><rect width="16" height="16" rx="2" fill="#f7941d"/><path d="M5 11l6-6M4 9l-0.5 0.5a2 2 0 0 0 3 3L7 12M12 7l0.5-0.5a2 2 0 0 0-3-3L9 4" stroke="#141414" stroke-width="1.4" fill="none" stroke-linecap="round"/></svg>
          www.website.example
        </li>
      </ul>
    </div>
  </section>
  <section class="card card--back" aria-label="Business card back">
    <div class="back-mark"></div>
    <p class="back-name">Kestrel Homes</p>
  </section>
</main>
</body>
</html>
```